Web design for a honey company

We are a honey retailing company currently looking for creative design for 3 pages of our existing e-commerce website which can be found here www.alpha.tolvenmarsk.co.nz. The designs need to be responsive i.e. presented in both desktop and mobile versions. We want to use the existing page color pallet, however any fonts can be used. Please use the texts and graphic content in the attachment files provided. For more detailed instructions please. The page does not require coding, the output files should be provided as layered and editable PSD.<br/><br/>Task 2: design 2 home page banners. Images, texts and the concept provided in the "layout structure" file. <br/><br/>The web designs should be presented in both desktop and mobile versions. We are looking for professional designer submissions only!

Target Market(s)

Hi-end consumers
Health conscious consumers

Number of Pages Required

3 page

Requirements
Must have
• 50% of images supplied along + any suggested stock images.
• Supplied texts integrated in the designs.
• Please only use the product images we have provided!
Should not have
• Clipart vector bees, vector honey slots or combs.
• No images of honey in glass jars!
• Do not use images of the traditional honey wooden spoons!
• Do not use images of any other but Manuka flower!

```html
<!DOCTYPE html>
<html lang="en">
<head>
<meta charset="utf-8">
<title>Tolvenmarsk – Manuka Honey</title>
<link href="https://fonts.googleapis.com/css2?family=Karla:wght@400;500;700&family=Roboto:wght@400;500&display=swap" rel="stylesheet">
<style>
:root{
  --ink:#111;
  --bar:#0d0d0d;
  --nav:#2a2a2a;
  --gold:#e7bf62;
  --gold-soft:#f8dc9b;
  --gold-pale:#fde8b4;
  --text:#222;
  --muted:#555;
  --grey-bg:#f2f2f2;
  --white:#fff;
  --green:#2f9a3a;
  --star:#f39a1c;
}
*{box-sizing:border-box;margin:0;padding:0}
html,body{width:1200px;height:3247px;overflow:hidden}
body{position:relative;background:var(--white);font-family:"Roboto",Arial,sans-serif;color:var(--text)}
.abs{position:absolute}
h1,h2,h3,.karla{font-family:"Karla",Arial,sans-serif}

/* top bar */
.topbar{left:0;top:0;width:1200px;height:42px;background:var(--bar);color:#fff;font-family:"Karla",sans-serif;font-weight:700;font-size:12px;display:flex;align-items:center;justify-content:space-between;padding:0 89px}
.topbar nav a{color:#fff;text-decoration:none;margin-left:16px}

/* header */
.header{left:0;top:42px;width:1200px;height:107px;background:var(--nav);display:flex;align-items:center;padding:0 86px;justify-content:space-between}
.brand{display:flex;align-items:center;gap:10px;font-family:"Karla",sans-serif;font-weight:700;font-size:22px;color:var(--gold);letter-spacing:1px}
.brand .dot{width:14px;height:14px;border-radius:50%;background:var(--gold)}
.menu{display:flex;gap:44px;font-family:"Karla",sans-serif;font-size:19px;color:#fff}
.menu span{display:flex;align-items:center;gap:8px;position:relative}
.menu .active::after{content:"";position:absolute;left:0;right:0;bottom:-8px;height:2px;background:var(--gold)}
.menu svg{width:12px;height:12px;margin-left:10px}

/* hero */
.hero{left:0;top:149px;width:1200px;height:582px;background:linear-gradient(100deg,#2d3236 0%,#4e5559 35%,#8a8f8e 58%,#c2a24c 66%,#c9c5b8 78%,#9aa0a1 100%)}
.hero-photo{position:absolute;inset:0}
.hero-copy{position:absolute;left:89px;top:182px;color:#fff}
.hero-copy h1{font-size:52px;font-weight:700;letter-spacing:2px}
.hero-copy p{font-size:17px;line-height:27px;width:420px;margin-top:16px}
.btn-start{display:inline-block;margin-top:22px;background:var(--gold);color:#1a1a1a;font-family:"Karla",sans-serif;font-weight:700;font-size:23px;letter-spacing:1px;padding:14px 32px;border-radius:30px}
.hero-dots{position:absolute;left:550px;bottom:12px;display:flex;gap:6px}
.hero-dots i{width:7px;height:7px;border-radius:50%;background:#777}
.hero-dots i.on{background:var(--gold)}

/* featured */
.featured{left:0;top:847px;width:1200px;height:680px;background:radial-gradient(ellipse at 15% 20%,#fdf3d6 0%,transparent 40%),radial-gradient(ellipse at 85% 80%,#fdf0cc 0%,transparent 40%),linear-gradient(#fffdf6,#fff9ea)}
.section-title{font-family:"Karla",sans-serif;font-weight:700;font-size:35px;letter-spacing:1.5px;color:var(--ink);text-align:center}
.featured .section-title{position:absolute;top:62px;width:100%}
.card{position:absolute;top:136px;width:328px;height:431px;background:#f7f7f7;box-shadow:0 2px 8px rgba(0,0,0,.18);text-align:center;padding:8px}
.card.hl{background:var(--gold-soft)}
.card .shot{height:199px;position:relative;background:linear-gradient(180deg,#ffffff 0%,#ececec 100%)}
.tag{position:absolute;left:0;bottom:0;padding:5px 20px;font-size:17px}
.tag.gold{background:var(--gold);color:#222}
.tag.green{background:var(--green);color:#fff}
.card h3{font-weight:500;font-size:23px;line-height:35px;margin-top:12px;letter-spacing:.5px;color:#111}
.stars{display:flex;justify-content:center;gap:8px;margin-top:4px}
.stars svg{width:28px;height:28px}
.price{font-family:"Karla",sans-serif;font-weight:500;font-size:21px;margin-top:12px;color:#111}
.card-btns{display:flex;justify-content:center;gap:15px;margin-top:18px}
.card-btns span{width:140px;height:41px;border-radius:21px;display:flex;align-items:center;justify-content:center;font-size:17px}
.b-buy{background:var(--gold-pale);color:#111;font-family:"Karla",sans-serif}
.b-cart{background:var(--gold);color:#fff}
.slider-dots{position:absolute;top:615px;left:576px;display:flex;gap:6px}
.slider-dots i{width:14px;height:14px;border:1.6px solid #111;border-radius:50%}
.slider-dots i.on{background:#111}

/* media */
.media-title{left:0;top:1636px;width:1200px}
.mcard{position:absolute}
.ph{position:relative}
.label{position:absolute;left:0;bottom:0;background:var(--gold);color:#fff;font-family:"Karla",sans-serif;font-weight:700;font-size:21px;letter-spacing:1px;padding:4px 0;text-align:center}
.mcard h3{font-size:22px;font-weight:500;letter-spacing:.8px;color:#111;margin-top:14px;white-space:nowrap}
.meta{display:flex;align-items:center;gap:12px;font-size:13.5px;color:#222;margin-top:10px;white-space:nowrap}
.meta span{display:flex;align-items:center;gap:6px;white-space:nowrap}
.meta svg{width:13px;height:13px;flex:none}
.mcard p{font-size:14px;line-height:22px;color:#222;margin-top:8px;text-align:justify}
.more{display:flex;align-items:center;gap:14px;font-size:13px;color:var(--gold);margin-top:14px;letter-spacing:.5px}
.more svg{width:16px;height:8px}
.play{position:absolute;left:180px;top:118px;width:22px;height:22px;border-radius:50%;background:#fff;display:flex;align-items:center;justify-content:center}

/* newsletter */
.newsletter{left:0;top:2512px;width:1200px;height:326px;background:var(--grey-bg);text-align:center}
.newsletter .section-title{margin-top:55px;word-spacing:8px}
.newsletter p{font-size:16.5px;line-height:28px;color:#666;width:720px;margin:16px auto 0}
.subscribe{width:544px;height:74px;margin:30px auto 0;border:1.5px solid #999;border-radius:37px;display:flex;align-items:center;justify-content:space-between;padding:0 6px 0 20px;background:#fff}
.subscribe span{font-size:17px;color:#444}
.subscribe b{width:172px;height:60px;border-radius:30px;background:var(--gold);display:flex;align-items:center;justify-content:center;font-family:"Karla",sans-serif;font-weight:700;font-size:18px;letter-spacing:1px;color:#111}

/* footer */
.footer{left:0;top:2838px;width:1200px;height:409px;background:#000;color:#fff}
.f-brand{position:absolute;left:92px;top:92px;width:310px;height:182px;display:flex;align-items:center;justify-content:center;gap:12px;font-family:"Karla",sans-serif;font-weight:700;font-size:32px;color:var(--gold);letter-spacing:1.5px}
.f-brand .dot{width:18px;height:18px;border-radius:50%;background:var(--gold)}
.f-links{position:absolute;top:112px;font-family:"Karla",sans-serif;font-size:19px;line-height:37px}
.pay{position:absolute;top:270px;left:475px;display:flex;gap:18px;align-items:center}
.pay i{display:block;border-radius:5px}
.copy{position:absolute;top:352px;width:100%;text-align:center;font-family:"Karla",sans-serif;font-size:16px}
</style>
</head>
<body>

<header class="abs topbar">
  <span>OUR PHONE NUMBER: + (64) 210004821</span>
  <nav><a>MY ACCOUNT</a><a>CART</a><a>OUR LOCATION</a><a>CONTACT US</a></nav>
</header>

<div class="abs header">
  <div class="brand"><span class="dot"></span>TOLVENMARSK</div>
  <nav class="menu">
    <span class="active">Home</span>
    <span>Shop<svg viewBox="0 0 12 12"><path d="M2 4l4 4 4-4" fill="none" stroke="#fff" stroke-width="1.6"/></svg></span>
    <span>Quality<svg viewBox="0 0 12 12"><path d="M2 4l4 4 4-4" fill="none" stroke="#fff" stroke-width="1.6"/></svg></span>
    <span>About</span>
    <span>Tolvenmarsk<svg viewBox="0 0 12 12"><path d="M2 4l4 4 4-4" fill="none" stroke="#fff" stroke-width="1.6"/></svg></span>
    <span>Contact Us</span>
  </nav>
</div>

<section class="abs hero">
  <div class="hero-photo" role="img" aria-label="Beekeeper in a protective suit holding a honeycomb frame over hives"></div>
  <div class="hero-copy">
    <h1>TOLVENMARSK</h1>
    <p>Lorem ipsum dolor sit amet, consectetur adipiscing elit, sed do eiusmod tempor incididunt ut labore et</p>
    <span class="btn-start">GET STARTED</span>
  </div>
  <div class="hero-dots"><i></i><i class="on"></i><i></i></div>
</section>

<section class="abs featured">
  <h2 class="section-title">FEATURED PRODUCTS</h2>

  <article class="card" style="left:88px">
    <div class="shot" role="img" aria-label="Product photo: MGO 800+ Manuka honey"></div>
    <h3>MGO 800+<br>MANUKA HONEY</h3>
    <div class="stars">
      <svg viewBox="0 0 24 24"><path fill="var(--star)" d="M12 1l3.3 7 7.7.9-5.7 5.2 1.6 7.6L12 17.9 5.1 21.7l1.6-7.6L1 8.9 8.7 8z"/></svg>
      <svg viewBox="0 0 24 24"><path fill="var(--star)" d="M12 1l3.3 7 7.7.9-5.7 5.2 1.6 7.6L12 17.9 5.1 21.7l1.6-7.6L1 8.9 8.7 8z"/></svg>
      <svg viewBox="0 0 24 24"><path fill="var(--star)" d="M12 1l3.3 7 7.7.9-5.7 5.2 1.6 7.6L12 17.9 5.1 21.7l1.6-7.6L1 8.9 8.7 8z"/></svg>
      <svg viewBox="0 0 24 24"><path fill="var(--star)" d="M12 1l3.3 7 7.7.9-5.7 5.2 1.6 7.6L12 17.9 5.1 21.7l1.6-7.6L1 8.9 8.7 8z"/></svg>
    </div>
    <div class="price">USD $25.00 – $129.00</div>
    <div class="card-btns"><span class="b-buy">BUY NOW</span><span class="b-cart">ADD TO CART</span></div>
  </article>

  <article class="card hl" style="left:436px">
    <div class="shot" role="img" aria-label="Product photo: MGO 500+ Manuka honey"><span class="tag gold">23% DISCOUNT</span></div>
    <h3>MGO 500+<br>MANUKA HONEY</h3>
    <div class="stars">
      <svg viewBox="0 0 24 24"><path fill="var(--star)" d="M12 1l3.3 7 7.7.9-5.7 5.2 1.6 7.6L12 17.9 5.1 21.7l1.6-7.6L1 8.9 8.7 8z"/></svg>
      <svg viewBox="0 0 24 24"><path fill="var(--star)" d="M12 1l3.3 7 7.7.9-5.7 5.2 1.6 7.6L12 17.9 5.1 21.7l1.6-7.6L1 8.9 8.7 8z"/></svg>
      <svg viewBox="0 0 24 24"><path fill="var(--star)" d="M12 1l3.3 7 7.7.9-5.7 5.2 1.6 7.6L12 17.9 5.1 21.7l1.6-7.6L1 8.9 8.7 8z"/></svg>
      <svg viewBox="0 0 24 24"><path fill="var(--star)" d="M12 1l3.3 7 7.7.9-5.7 5.2 1.6 7.6L12 17.9 5.1 21.7l1.6-7.6L1 8.9 8.7 8z"/></svg>
      <svg viewBox="0 0 24 24"><path fill="var(--star)" d="M12 1l3.3 7 7.7.9-5.7 5.2 1.6 7.6L12 17.9 5.1 21.7l1.6-7.6L1 8.9 8.7 8z"/></svg>
    </div>
    <div class="price">USD $25.00 – $35.00</div>
    <div class="card-btns"><span class="b-buy">BUY NOW</span><span class="b-cart">ADD TO CART</span></div>
  </article>

  <article class="card" style="left:784px">
    <div class="shot" role="img" aria-label="Product photo: MGO 300+ Manuka honey"><span class="tag green">FREE DELIVERY</span></div>
    <h3>MGO 300+<br>MANUKA HONEY</h3>
    <div class="stars">
      <svg viewBox="0 0 24 24"><path fill="var(--star)" d="M12 1l3.3 7 7.7.9-5.7 5.2 1.6 7.6L12 17.9 5.1 21.7l1.6-7.6L1 8.9 8.7 8z"/></svg>
      <svg viewBox="0 0 24 24"><path fill="var(--star)" d="M12 1l3.3 7 7.7.9-5.7 5.2 1.6 7.6L12 17.9 5.1 21.7l1.6-7.6L1 8.9 8.7 8z"/></svg>
      <svg viewBox="0 0 24 24"><path fill="var(--star)" d="M12 1l3.3 7 7.7.9-5.7 5.2 1.6 7.6L12 17.9 5.1 21.7l1.6-7.6L1 8.9 8.7 8z"/></svg>
      <svg viewBox="0 0 24 24"><path fill="var(--star)" d="M12 1l3.3 7 7.7.9-5.7 5.2 1.6 7.6L12 17.9 5.1 21.7l1.6-7.6L1 8.9 8.7 8z"/></svg>
      <svg viewBox="0 0 24 24"><path fill="var(--star)" d="M12 1l3.3 7 7.7.9-5.7 5.2 1.6 7.6L12 17.9 5.1 21.7l1.6-7.6L1 8.9 8.7 8z"/></svg>
    </div>
    <div class="price">USD $25.00 – USD $35.00</div>
    <div class="card-btns"><span class="b-buy">BUY NOW</span><span class="b-cart">ADD TO CART</span></div>
  </article>

  <div class="slider-dots"><i></i><i class="on"></i><i></i></div>
</section>

<h2 class="abs section-title media-title">MEDIA TOLVENMARSK</h2>

<!-- video -->
<article class="mcard" style="left:91px;top:1709px;width:380px">
  <div class="ph" style="height:263px;background:linear-gradient(135deg,#cfd2d1,#9ea4a6 50%,#e6e3de)" role="img" aria-label="Video still of a honey worker in a processing room">
    <span class="play"><svg width="10" height="10" viewBox="0 0 10 10"><path d="M2 1l7 4-7 4z" fill="#333"/></svg></span>
    <span class="label" style="width:162px">VIDEO</span>
  </div>
  <div style="padding-left:10px">
    <h3>FINIBUS BONORUM</h3>
    <div class="meta">
      <span><svg viewBox="0 0 14 14"><rect x="1" y="2" width="12" height="11" fill="none" stroke="var(--gold)" stroke-width="1.5"/><path d="M1 5h12" stroke="var(--gold)" stroke-width="1.5"/></svg>JAN 31, 2020</span>
      <span><svg viewBox="0 0 14 14"><circle cx="7" cy="4" r="3" fill="var(--gold)"/><path d="M1 14c0-4 3-6 6-6s6 2 6 6z" fill="var(--gold)"/></svg>Tolvenmarsk</span>
      <span><svg viewBox="0 0 14 14"><circle cx="7" cy="7" r="5.5" fill="none" stroke="var(--gold)" stroke-width="1.5"/><path d="M7 4v3l2 2" fill="none" stroke="var(--gold)" stroke-width="1.5"/></svg>03.00 Mins</span>
    </div>
    <p>Lorem ipsum dolor sit amet, consectetur adipiscing elit, sed do eiusmod tempor incididunt ut</p>
    <div class="more">VIEW MORE <svg viewBox="0 0 16 8"><path d="M0 4h14M11 1l3 3-3 3" fill="none" stroke="var(--gold)" stroke-width="1.3"/></svg></div>
  </div>
</article>

<!-- articles -->
<article class="mcard" style="left:486px;top:1709px;width:304px">
  <div class="ph" style="height:190px;background:linear-gradient(135deg,#8a4a25,#b8743c 50%,#e9e4da)" role="img" aria-label="Beekeeper holding a honeycomb frame beside a wooden shed">
    <span class="label" style="width:162px">ARTICLES</span>
  </div>
  <div style="padding-left:6px">
    <h3>FINIBUS BONORUM</h3>
    <div class="meta">
      <span><svg viewBox="0 0 14 14"><rect x="1" y="2" width="12" height="11" fill="none" stroke="var(--gold)" stroke-width="1.5"/><path d="M1 5h12" stroke="var(--gold)" stroke-width="1.5"/></svg>JAN 21, 2020</span>
      <span><svg viewBox="0 0 14 14"><circle cx="7" cy="4" r="3" fill="var(--gold)"/><path d="M1 14c0-4 3-6 6-6s6 2 6 6z" fill="var(--gold)"/></svg>Tolvenmarsk</span>
      <span><svg viewBox="0 0 14 14"><path d="M1 2h12v8H6l-3 3v-3H1z" fill="var(--gold)"/></svg>34 COM</span>
    </div>
    <p>Lorem ipsum dolor sit amet, consectetur</p>
    <div class="more">VIEW MORE <svg viewBox="0 0 16 8"><path d="M0 4h14M11 1l3 3-3 3" fill="none" stroke="var(--gold)" stroke-width="1.3"/></svg></div>
  </div>
</article>

<!-- news -->
<article class="mcard" style="left:808px;top:1709px;width:302px">
  <div class="ph" style="height:190px;background:linear-gradient(135deg,#a8b35a,#c98f3a 50%,#5a3b20)" role="img" aria-label="Bees flying around wooden hives in sunlight">
    <span class="label" style="width:162px">NEWS</span>
  </div>
  <div style="padding-left:9px">
    <h3>FINIBUS BONORUM</h3>
    <div class="meta">
      <span><svg viewBox="0 0 14 14"><rect x="1" y="2" width="12" height="11" fill="none" stroke="var(--gold)" stroke-width="1.5"/><path d="M1 5h12" stroke="var(--gold)" stroke-width="1.5"/></svg>JAN 11, 2020</span>
      <span><svg viewBox="0 0 14 14"><circle cx="7" cy="4" r="3" fill="var(--gold)"/><path d="M1 14c0-4 3-6 6-6s6 2 6 6z" fill="var(--gold)"/></svg>Tolvenmarsk</span>
      <span><svg viewBox="0 0 14 14"><path d="M1 7c2-4 10-4 12 0-2 4-10 4-12 0z" fill="none" stroke="var(--gold)" stroke-width="1.4"/><circle cx="7" cy="7" r="2" fill="var(--gold)"/></svg>400 VIEWS</span>
    </div>
    <p>Lorem ipsum dolor sit amet, consectetur</p>
    <div class="more">VIEW MORE <svg viewBox="0 0 16 8"><path d="M0 4h14M11 1l3 3-3 3" fill="none" stroke="var(--gold)" stroke-width="1.3"/></svg></div>
  </div>
</article>

<!-- resources -->
<article class="mcard" style="left:485px;top:2041px;width:624px">
  <div class="ph" style="height:232px;background:linear-gradient(120deg,#4f7a34,#9dbb7a 40%,#eef0e6 65%,#6d8f45)" role="img" aria-label="Beekeeper with a frame among flowering trees and hives">
    <span class="label" style="width:199px">RESOURCES</span>
  </div>
  <div style="padding-left:10px">
    <h3>FINIBUS BONORUM ET MALORUM</h3>
    <p>Lorem ipsum dolor sit amet, consectetur adipiscing elit, sed do eiusmod tempor incididunt ut labore et dolore magna aliqua. Ut enim ad minim veniam, quis nostrud exercitation ullamco laboris nisi ut aliquip ex ea commodo consequat.</p>
    <div class="more">VIEW MORE <svg viewBox="0 0 16 8"><path d="M0 4h14M11 1l3 3-3 3" fill="none" stroke="var(--gold)" stroke-width="1.3"/></svg></div>
  </div>
</article>

<!-- blog -->
<article class="mcard" style="left:91px;top:2152px;width:380px">
  <div class="ph" style="height:151px;background:linear-gradient(120deg,#3d6b2a,#86a84e 45%,#5278a8 75%,#2f4f7a)" role="img" aria-label="Beekeeper inspecting a frame in green foliage">
    <span class="label" style="width:162px">BLOG</span>
  </div>
  <div style="padding-left:8px">
    <h3>FINIBUS BONORUM</h3>
    <div class="meta">
      <span><svg viewBox="0 0 14 14"><rect x="1" y="2" width="12" height="11" fill="none" stroke="var(--gold)" stroke-width="1.5"/><path d="M1 5h12" stroke="var(--gold)" stroke-width="1.5"/></svg>JAN 15, 2020</span>
      <span><svg viewBox="0 0 14 14"><circle cx="7" cy="4" r="3" fill="var(--gold)"/><path d="M1 14c0-4 3-6 6-6s6 2 6 6z" fill="var(--gold)"/></svg>Tolvenmarsk</span>
    </div>
    <p>Lorem ipsum dolor sit amet, consectetur adipiscing</p>
    <div class="more" style="margin-top:6px">VIEW MORE <svg viewBox="0 0 16 8"><path d="M0 4h14M11 1l3 3-3 3" fill="none" stroke="var(--gold)" stroke-width="1.3"/></svg></div>
  </div>
</article>

<section class="abs newsletter">
  <h2 class="section-title">NEWSLETTER SUBSCRIPTION</h2>
  <p>Lorem ipsum dolor sit amet, consectetur adipiscing elit, sed do eiusmod tempor incididunt ut labore et dolore magna aliqua.</p>
  <div class="subscribe"><span>Enter the email</span><b>SIGN UP</b></div>
</section>

<footer class="abs footer">
  <div class="f-brand"><span class="dot"></span>TOLVENMARSK</div>
  <div class="f-links" style="left:520px">Shop<br>Terms &amp; Conditions<br>Privacy Policy</div>
  <div class="f-links" style="left:763px">FAQs<br>Partnership enquiries</div>
  <div class="pay" aria-label="Accepted payment methods">
    <i style="width:116px;height:36px;background:#2a4c8f"></i>
    <i style="width:54px;height:36px;background:#e0562c"></i>
    <i style="width:64px;height:38px;background:#e8edf5;border-bottom:6px solid #e7a52e"></i>
  </div>
  <div class="copy">(c) 2020 TOLVENMARSK. | All Rights Reserved</div>
</footer>

</body>
</html>
```